Corporate Travel Technology Company needs new Business Card design

We need a new business card design to reflect our re-branded company. Our company is called Tolven (pronounced tolvenn) and we provide Business Intelligence and mobile travel management solutions for the corporate travel industry. Our multinational customers use our solutions to manage large travel budgets and frequent travellers, as well as to save money and reduce risk. We'd like to see designs that use the blue and green palette as well as our corporate logo (attached below). The design should communicate innovation, insight, forward thinking, contemporary, trusted.

Target Market(s)

Large multinational corporates and Travel Agencies.

Industry/Entity Type

Business

Contact Information for Business Card

Rosalind Mercer
Chief Executive
Tolven
Phone number - +61 (0)2 8134 2907
Email address - rosalind.mercer@tolven-example.com
Mobile number - +61 (0)438 516 702
www.tolven-example.com

Font styles to use
Other font styles liked:
• Please use font as close to corporate logo as possible

Colors
0255a3
0393ce
00a990
33b8a4
33a6d7
3176b5

Requirements
Must have
• Please include the words;
• Mobile Travel Management
• Accelerating Travel Business Insights
• Use corporate logo - although icon can be stylised if needed

```html
<!DOCTYPE html>
<html lang="en">
<head>
<meta charset="utf-8">
<title>Tolven – Business Card</title>
<link href="https://fonts.googleapis.com/css2?family=Open+Sans:wght@400;600;700&display=swap" rel="stylesheet">
<style>
  :root {
    --page-bg: #ecebe8;
    --teal: #00a990;
    --blue: #0393ce;
    --ink: #4b5858;
    --text: #222222;
    --white: #ffffff;
    --card-shadow: 0 10px 30px rgba(0, 0, 0, 0.18);
  }
  * { box-sizing: border-box; margin: 0; padding: 0; }
  html, body {
    width: 1200px; height: 900px; overflow: hidden;
    background: var(--page-bg);
    font-family: "Open Sans", Arial, sans-serif;
  }
  .canvas {
    width: 1200px; height: 900px;
    display: flex; flex-direction: column;
    align-items: center; justify-content: center; gap: 48px;
  }
  .card {
    width: 680px; height: 388px;
    position: relative;
    box-shadow: var(--card-shadow);
  }

  /* Wordmark */
  .brand {
    position: absolute;
    display: flex; align-items: center; gap: 16px;
    font-weight: 600; letter-spacing: -1px; line-height: 1;
    white-space: nowrap;
  }
  .brand__dot { border-radius: 50%; flex: none; background: currentColor; }

  /* Front */
  .card--front { background: var(--teal); color: var(--white); }
  .card--front .brand { left: 50%; top: 112px; transform: translateX(-50%); font-size: 88px; }
  .card--front .brand__dot { width: 18px; height: 18px; }
  .taglines {
    position: absolute; left: 0; right: 0; top: 262px;
    list-style: none;
    font-weight: 600; font-size: 18px; line-height: 1.4;
  }
  .taglines li { display: flex; align-items: center; justify-content: center; gap: 10px; }
  .taglines svg { width: 15px; height: 13px; flex: none; }

  /* Back */
  .card--back { background: var(--white); }
  .card--back .brand { left: 240px; top: 100px; font-size: 84px; color: var(--ink); }
  .card--back .brand__dot { width: 17px; height: 17px; }
  .contacts {
    position: absolute; left: 372px; top: 222px;
    list-style: none; font-size: 14px; line-height: 24px; color: var(--text);
    white-space: nowrap;
  }
  .contacts li { display: flex; align-items: center; gap: 12px; }
  .contacts svg { width: 13px; height: 13px; flex: none; color: var(--blue); }
  .holder { position: absolute; left: 60px; top: 282px; text-align: right; }
  .holder__name { font-size: 22px; font-weight: 600; color: var(--blue); line-height: 1.15; }
  .holder__role { font-size: 15px; color: var(--text); }
</style>
</head>
<body>
<main class="canvas">

  <section class="card card--front">
    <div class="brand"><span class="brand__dot"></span>Tolven</div>
    <ul class="taglines">
      <li><svg viewBox="0 0 16 14"><path d="M2 4 L5 1 H11 L14 4 L8 13 Z" fill="none" stroke="currentColor" stroke-width="1.6"/></svg>Mobile Travel Management</li>
      <li><svg viewBox="0 0 16 14"><path d="M2 4 L5 1 H11 L14 4 L8 13 Z" fill="none" stroke="currentColor" stroke-width="1.6"/></svg>Accelerating Travel Business Insights</li>
    </ul>
  </section>

  <section class="card card--back">
    <div class="brand"><span class="brand__dot"></span>Tolven</div>
    <ul class="contacts">
      <li><svg viewBox="0 0 16 16"><path d="M3 1 L6 1 L7 5 L5 6.5 C6 9 7 10 9.5 11 L11 9 L15 10 L15 13 C15 14 14 15 13 15 C6 14 2 10 1 3 C1 2 2 1 3 1 Z" fill="currentColor"/></svg>+61 (0)2 8134 2907</li>
      <li><svg viewBox="0 0 16 16"><rect x="4" y="1" width="8" height="14" rx="1.5" fill="none" stroke="currentColor" stroke-width="1.8"/><rect x="6" y="4" width="4" height="4" fill="currentColor"/></svg>+61 (0)438 516 702</li>
      <li><svg viewBox="0 0 16 16"><rect x="1" y="3" width="14" height="10" fill="currentColor"/><path d="M1 3 L8 9 L15 3" fill="none" stroke="#fff" stroke-width="1.4"/></svg>rosalind.mercer@tolven-example.com</li>
      <li><svg viewBox="0 0 16 16"><g fill="none" stroke="currentColor" stroke-width="2"><rect x="1.5" y="7" width="7" height="4" rx="2" transform="rotate(-45 5 9)"/><rect x="7.5" y="5" width="7" height="4" rx="2" transform="rotate(-45 11 7)"/></g></svg>www.tolven-example.com</li>
    </ul>
    <div class="holder">
      <p class="holder__name">Rosalind Mercer</p>
      <p class="holder__role">Chief Executive</p>
    </div>
  </section>

</main>
</body>
</html>
```